KLV Plant Services

We are a heavy diesel mechanical business with additional air con certificates, remapping engine rebuilt

Contact Information for Business Card

Company Name, Director Name, Managing Director, Contact details, email and website

Font styles to use
Serif
Script

```html
<!DOCTYPE html>
<html lang="en">
<head>
<meta charset="utf-8">
<title>KLV Plant Services – Business Card</title>
<link rel="stylesheet" href="https://fonts.googleapis.com/css2?family=Arimo:wght@400;700&display=swap">
<style>
  :root {
    --backdrop: #dcdcdc;
    --card-light: #f4f4f6;
    --card-dark: #000000;
    --navy: #0f0f6e;
    --ink: #1c1c1c;
    --muted: #555555;
    --white: #ffffff;
  }
  * { margin: 0; padding: 0; box-sizing: border-box; }
  html, body {
    width: 1200px; height: 1040px; overflow: hidden;
    background: var(--backdrop);
    font-family: "Arimo", Arial, sans-serif;
  }
  .canvas { position: relative; width: 1200px; height: 1040px; }
  .card {
    position: absolute; left: 285px; width: 645px; height: 365px;
    border-radius: 16px; overflow: hidden;
  }
  .card--front { top: 130px; background: var(--card-light); }
  .card--back { top: 567px; background: var(--card-dark); }

  .brand {
    position: absolute; display: flex; align-items: center; gap: 10px;
    font-weight: 700; white-space: nowrap;
  }
  .brand__dot { border-radius: 50%; flex: none; }
  .card--front .brand { right: 50px; top: 98px; color: var(--navy); font-size: 26px; }
  .card--front .brand__dot { width: 18px; height: 18px; background: var(--navy); }
  .card--back .brand {
    left: 0; right: 0; top: 160px; justify-content: center;
    color: var(--white); font-size: 40px;
  }
  .card--back .brand__dot { width: 26px; height: 26px; background: var(--white); }

  .person { position: absolute; left: 43px; top: 206px; }
  .person__name { color: var(--navy); font-size: 24px; font-weight: 700; line-height: 1.1; }
  .person__role { color: var(--muted); font-size: 15.5px; margin-top: 3px; }

  .divider {
    position: absolute; left: 43px; width: 553px; top: 257px;
    height: 1px; background: var(--ink);
  }
  .contacts {
    position: absolute; left: 43px; top: 270px; list-style: none;
    color: var(--ink); font-size: 16px; line-height: 20px;
  }
  .contacts li { display: flex; align-items: center; gap: 7px; }
  .contacts svg { width: 12px; height: 12px; fill: var(--navy); flex: none; }
  .address {
    position: absolute; right: 49px; top: 272px; text-align: right;
    color: var(--ink); font-size: 16px; line-height: 20px; font-style: normal;
  }
  .footer-band { position: absolute; left: 0; bottom: 0; width: 645px; height: 17px; }
</style>
</head>
<body>
<main class="canvas">
  <section class="card card--front" aria-label="Business card front">
    <div class="brand"><span class="brand__dot"></span>KLV Plant Services</div>

    <div class="person">
      <h1 class="person__name">Owen Hartley</h1>
      <p class="person__role">Managing Director</p>
    </div>
    <div class="divider"></div>

    <ul class="contacts">
      <li><svg viewBox="0 0 24 24"><path d="M6.6 10.8a15.1 15.1 0 0 0 6.6 6.6l2.2-2.2a1 1 0 0 1 1-.25 11.4 11.4 0 0 0 3.6.57 1 1 0 0 1 1 1V20a1 1 0 0 1-1 1A17 17 0 0 1 3 4a1 1 0 0 1 1-1h3.5a1 1 0 0 1 1 1c0 1.25.2 2.45.57 3.6a1 1 0 0 1-.25 1z"/></svg>(555) 0142-7781</li>
      <li><svg viewBox="0 0 24 24"><path d="M2 5h20v14H2zM4 7v.4l8 5 8-5V7zm0 2.8V17h16V9.8l-8 5z"/></svg>name@KLV.com</li>
      <li><svg viewBox="0 0 24 24"><circle cx="12" cy="12" r="10"/></svg>www.KLV.com</li>
    </ul>

    <address class="address">2190 Ashgrove Lane<br>Brookfield, NY 11020</address>

    <svg class="footer-band" viewBox="0 0 645 17" preserveAspectRatio="none" aria-hidden="true">
      <polygon points="0,0 420,0 415,17 0,17" fill="var(--navy)"/>
      <polygon points="426,0 645,0 645,17 421,17" fill="var(--card-dark)"/>
    </svg>
  </section>

  <section class="card card--back" aria-label="Business card back">
    <div class="brand"><span class="brand__dot"></span>KLV Plant Services</div>
  </section>
</main>
</body>
</html>
```